Surya Namaskar/Sun salutation theme based 12 months desk calendar for 2016 for an indian company

1. We are a corporate support services provider, providing services in Security Management, Fire Safety Management, facility management & HR Services based out of India. pls check website: www.brelvanta.co.in
2. Need a complete 12 months desk calendar design layout for 2016 including introductory page & end page,which can then be given for printing straightaway. The calendar should be so designed that when we open any month on the front side, the back side should also give out just the same month dates layout with space to note down any important work on a date etc..All important indian festivals, gazetted hoildays should be mentioned. Any information required can be provided by us
3. Since we give this calendars as part of new year gifts, our calendar has to compete for client desk space with other calendars, it must really be very sophisticated, sleek and attractive
4. Company logo, company contact details, website details and company works must be included in the calendar but in subtle, unobtrusive way. Few details like company logo etc, can be there on all pages.Am uploading some details, rest can be taken from the website, or can be provided
5. Calendar size should be aprx 17 cm * 17 cm including the space needed for spiral. Format should be CDR Ver13 or PDF
6. Theme: Surya Namaskar poses/Sun Salutation poses. These are twelve yoga poses, prescribed for mind /body rejuvenation. Poses 1-12 should be on months Jan16 to Dec 16. A very brief writeup on the same including the relevant mantras may also be included on the page
7. Any query , please mail to rohan.mehtra@brelvanta.co.in

Target Market(s)

corporate middle & senior management MNC clients

Industry/Entity Type

Security

Requirements
Must have
• 1.company logos/contact & website details/company works with related photographs.
• 2. surya namaskar poses with a very small brief/health benefit on poses/related mantras
• 3. Indian gazetted holidays & festivals earmarked
• 4. recommendation on the printing paper type & quality/colour of cardboard base & spiral binding
• 5. Attractive Top Introduction page & end page
Nice to have
• 1. photos of the company works
• 2. End page may be used for giving company details in details
• 3. Company logo on each page
• 4. The calendar goes to a variety of corporate clients including hotels, hospitals, shopping malls, manufacturing sector, clubs etc..just for info
• 5. Related photos/same model in all months
• 6. Beautiful Female models in poses
• 7. target audience : 95% male; majority age group: 35-55; middle & senior management
• However, very receptive to any new ideas. The designer has full liberty from our side. The final parameter is that the calendar should be so attractive that it can defeat any other desk calendar competition and win that one spot on the desk
• Any queries/details required, pls mail to rohan.mehtra@brelvanta.co.in
Should not have
• Religious overtones

```html
<!DOCTYPE html>
<html lang="en">
<head>
<meta charset="utf-8">
<title>January 2016 – Desk Calendar</title>
<link href="https://fonts.googleapis.com/css2?family=Josefin+Sans:wght@400;600&family=Alegreya:ital,wght@1,400;1,900&family=Montserrat:wght@700&display=swap" rel="stylesheet">
<style>
  :root {
    --cream: #f7e9cf;
    --teal: #2c6e64;
    --teal-text: #2a6a60;
    --sun-light: #f5d22c;
    --sun-deep: #f39c1f;
    --holiday: #f29a1a;
    --ink: #111111;
  }
  * { margin: 0; padding: 0; box-sizing: border-box; }
  html, body { width: 1200px; height: 1200px; overflow: hidden; background: var(--cream); }
  .page { position: relative; width: 1200px; height: 1200px; background: var(--cream); overflow: hidden; }
  .backdrop { position: absolute; inset: 0; }

  .month-title {
    position: absolute; left: 492px; width: 600px; top: 62px; text-align: center;
    font-family: "Josefin Sans", sans-serif; font-weight: 600; font-size: 58px;
    letter-spacing: 2px; color: var(--teal-text);
  }
  .weekdays {
    position: absolute; left: 492px; top: 136px; width: 600px;
    display: grid; grid-template-columns: repeat(7, 1fr);
    font-family: "Montserrat", sans-serif; font-weight: 700; font-size: 17px;
    color: var(--teal-text); text-align: center;
  }
  .month-grid {
    position: absolute; left: 492px; top: 166px; width: 600px; height: 515px;
    display: grid; grid-template-columns: repeat(7, 1fr); grid-template-rows: repeat(6, 1fr);
    border-top: 2px solid var(--teal); border-left: 2px solid var(--teal);
  }
  .day {
    border-right: 2px solid var(--teal); border-bottom: 2px solid var(--teal);
    padding: 4px 6px 0 0; text-align: right;
    font-family: "Josefin Sans", sans-serif; font-weight: 600; font-size: 25px;
    color: var(--teal-text); line-height: 1;
  }
  .day.holiday { color: var(--holiday); }

  .mantra-band {
    position: absolute; left: 456px; top: 717px; width: 490px; height: 157px;
    border-radius: 0 80px 80px 0;
    background: linear-gradient(90deg, var(--sun-deep) 0%, var(--sun-light) 45%, var(--sun-deep) 100%);
  }
  .mantra-title {
    position: absolute; left: 506px; top: 738px;
    font-family: "Alegreya", serif; font-style: italic; font-weight: 900;
    font-size: 44px; line-height: 58px; color: var(--ink);
  }
  .mantra-meaning {
    position: absolute; left: 505px; top: 905px;
    font-family: "Alegreya", serif; font-style: italic; font-weight: 400;
    font-size: 33px; line-height: 48px; color: var(--ink);
  }

  .brand {
    position: absolute; left: 1040px; top: 1120px; width: 150px; text-align: center;
    color: var(--cream); font-family: "Montserrat", sans-serif;
  }
  .brand-mark { display: inline-block; width: 22px; height: 22px; border-radius: 50%; background: var(--cream); margin-bottom: 4px; }
  .brand-name { font-size: 16px; font-weight: 700; letter-spacing: 0.5px; }
  .brand-tagline { font-size: 7px; font-weight: 700; margin-top: 2px; }
</style>
</head>
<body>
<main class="page">
  <svg class="backdrop" width="1200" height="1200" viewBox="0 0 1200 1200">
    <defs>
      <linearGradient id="pose-tone" x1="0" y1="0" x2="1" y2="1">
        <stop offset="0" stop-color="#ebe6dc"/>
        <stop offset="0.6" stop-color="#d9d3c7"/>
        <stop offset="1" stop-color="#c9c1b2"/>
      </linearGradient>
    </defs>
    <path role="img" aria-label="Photograph of a woman standing in the Pranamasana prayer pose against a white lattice wall"
      fill="url(#pose-tone)"
      d="M0,0 L372,0 C360,150 372,330 382,500 C392,700 402,880 372,925 C300,995 120,955 0,875 Z"/>
    <path class="sun-strip" fill="#f5b21f"
      d="M0,1035 C120,1090 260,1110 340,1092 C220,1128 90,1138 0,1132 Z"/>
    <path class="swoosh" fill="var(--teal)"
      d="M372,0 L432,0 C412,150 402,350 452,600 C484,770 472,1000 382,1062 C300,1105 150,1100 0,1092 L0,875 C120,955 300,995 372,925 C402,880 392,700 382,500 C372,330 360,150 372,0 Z"/>
    <circle class="corner-disc" cx="1245" cy="1250" r="250" fill="var(--teal)"/>
  </svg>

  <h1 class="month-title">JANUARY</h1>
  <div class="weekdays">
    <span>SUN</span><span>MON</span><span>TUE</span><span>WED</span><span>THU</span><span>FRI</span><span>SAT</span>
  </div>
  <div class="month-grid">
    <div class="day"></div><div class="day"></div><div class="day"></div><div class="day"></div><div class="day"></div><div class="day">1</div><div class="day">2</div>
    <div class="day">3</div><div class="day">4</div><div class="day">5</div><div class="day">6</div><div class="day">7</div><div class="day">8</div><div class="day">9</div>
    <div class="day">10</div><div class="day">11</div><div class="day">12</div><div class="day">13</div><div class="day">14</div><div class="day">15</div><div class="day">16</div>
    <div class="day">17</div><div class="day">18</div><div class="day">19</div><div class="day">20</div><div class="day">21</div><div class="day">22</div><div class="day">23</div>
    <div class="day">24</div><div class="day">25</div><div class="day holiday">26</div><div class="day">27</div><div class="day">28</div><div class="day">29</div><div class="day">30</div>
    <div class="day">31</div><div class="day"></div><div class="day"></div><div class="day"></div><div class="day"></div><div class="day"></div><div class="day"></div>
  </div>

  <div class="mantra-band"></div>
  <h2 class="mantra-title">1. Om Hraam<br>Mitraya Namah</h2>
  <p class="mantra-meaning">Prostration to Him<br>who is affectionate to all.</p>

  <div class="brand">
    <span class="brand-mark"></span>
    <div class="brand-name">BRELVANTA</div>
    <div class="brand-tagline">Your complete business companion</div>
    <div class="brand-tagline">Quality Certified Firm</div>
  </div>
</main>
</body>
</html>
```